Consulting company business cards

We have a base design, but would be willing to update. We have a new logo/"tag" that needs to be added. Current business card design is attached for reference into our "style."

Industry/Entity Type

Business

Contact Information for Business Card

Should contain name and title, office number, mobile number if appropriate, e-mail, website, physical address, and company logo.

Font styles to use
Other font styles liked:
• See current card design on KorvandBCard

Colors
0455a3
85acd3
aaaaaa

Requirements
Must have
• Our colors are navy blue, gray, and a lighter blue
Nice to have
• Design that I can easily drop in new names/titles as we hire employees.

```html
<!DOCTYPE html>
<html lang="en">
<head>
<meta charset="utf-8">
<title>Tarrow Business Card</title>
<link href="https://fonts.googleapis.com/css2?family=Oswald:wght@600&family=Source+Sans+3:wght@400;600;700&display=swap" rel="stylesheet">
<style>
  :root {
    --stage: #161616;
    --card-front: #f3f3f3;
    --navy: #0c3050;
    --navy-deep: #05324f;
    --navy-glow: #2f6689;
    --sky: #7fb0d0;
    --gray: #9a9a9a;
    --ink: #1a1a1a;
    --white: #ffffff;
  }
  html, body {
    margin: 0;
    width: 1200px;
    height: 900px;
    overflow: hidden;
    background: var(--stage);
    font-family: "Source Sans 3", "Myriad Pro", Arial, sans-serif;
  }
  .card {
    position: absolute;
    top: 184px;
    height: 490px;
    border-radius: 12px;
    box-sizing: border-box;
    overflow: hidden;
  }
  .card-front {
    left: 299px;
    width: 301px;
    background: var(--card-front);
    color: var(--ink);
    text-align: center;
  }
  .card-back {
    left: 645px;
    width: 304px;
    background: radial-gradient(circle at 50% 48%, var(--navy-glow) 0%, #1d5276 28%, var(--navy-deep) 68%);
  }
  .brand {
    position: absolute;
    top: 46px;
    left: 28px;
    width: 245px;
  }
  .brand-row {
    display: flex;
    align-items: center;
    gap: 10px;
  }
  .brand-name {
    font-family: "Oswald", "Arial Narrow", sans-serif;
    font-weight: 600;
    font-size: 60px;
    line-height: 1;
    letter-spacing: 1px;
    color: var(--navy);
    white-space: nowrap;
  }
  .brand-dot {
    flex: none;
    width: 46px;
    height: 46px;
    border-radius: 50%;
    background: var(--sky);
  }
  .brand-tag {
    margin-top: 6px;
    font-size: 12.5px;
    letter-spacing: 2.3px;
    color: var(--gray);
    text-align: left;
    white-space: nowrap;
  }
  .person {
    position: absolute;
    top: 256px;
    left: 0;
    right: 0;
  }
  .person-name {
    font-size: 19px;
    font-weight: 600;
    color: var(--navy);
    margin: 0;
    line-height: 24px;
  }
  .person-title {
    font-size: 14px;
    margin: 0;
    line-height: 18px;
  }
  .contact {
    list-style: none;
    padding: 0;
    margin: 26px 0 0;
    font-size: 14px;
    line-height: 20px;
  }
  .contact b { color: var(--navy); font-weight: 700; }
  .address {
    margin: 10px 0 0;
    font-size: 14px;
    line-height: 20px;
    font-style: normal;
  }
  .back-name {
    position: absolute;
    left: 0;
    right: 0;
    top: 362px;
    text-align: center;
    font-family: "Oswald", "Arial Narrow", sans-serif;
    font-weight: 600;
    font-size: 74px;
    line-height: 1;
    letter-spacing: 2px;
    color: var(--white);
    white-space: nowrap;
  }
</style>
</head>
<body>
  <section class="card card-front">
    <div class="brand">
      <div class="brand-row">
        <span class="brand-name">TARROW</span>
        <span class="brand-dot"></span>
      </div>
      <div class="brand-tag">A CLOUD CONSULTING COMPANY</div>
    </div>
    <div class="person">
      <p class="person-name">Dana Korvand</p>
      <p class="person-title">Office Manager</p>
      <ul class="contact">
        <li><b>O:</b> 555.014.2910</li>
        <li><b>F:</b> 555.014.2971</li>
        <li><b>E:</b> dkorvand@tarrowcloud.com</li>
        <li><b>W:</b> tarrowcloud.com</li>
      </ul>
      <address class="address">1875 W 40TH St Lakemont<br>Ohio 45099</address>
    </div>
  </section>
  <section class="card card-back">
    <div class="back-name">TARROW</div>
  </section>
</body>
</html>
```